TK Stationery - Modern Contemporary

Develop modern template for Letterhead and Stationery (business card, letterhead, envelopes) using the TK Logo and Icon

Colors
0054AA
0677BA
7BADD7
CADEEF
E8F1F8
00AB8E
00BBA5
67D7C9
C6EFE9
E9F9F6
EE7325
F08F49
F5BC92
FAE3D3
FDF4ED
6B429C
8869AF
B7A5CE
E3DAEB
F3F0F8

```html
<!DOCTYPE html>
<html lang="en">
<head>
<meta charset="utf-8">
<title>TK Letterhead</title>
<link href="https://fonts.googleapis.com/css2?family=Arimo&family=Questrial&display=swap" rel="stylesheet">
<style>
  :root {
    --backdrop: #cdcbcc;
    --paper: #ffffff;
    --navy: #2b304b;
    --green: #3aae6e;
    --ink: #505050;
    --footer-ink: #2b304b;
  }
  * { box-sizing: border-box; margin: 0; padding: 0; }
  html, body {
    width: 1173px; height: 1200px; overflow: hidden;
    background: var(--backdrop);
  }
  .letterhead {
    position: absolute; left: 230px; top: 96px;
    width: 714px; height: 1008px;
    background: var(--paper);
    box-shadow: 1px 2px 3px rgba(0,0,0,0.35);
  }
  .masthead {
    height: 92px; background: var(--navy);
    border-bottom: 5px solid var(--green);
    display: flex; align-items: center; justify-content: center; gap: 10px;
  }
  .brand {
    font-family: "Questrial", sans-serif;
    font-size: 36px; color: #ffffff; letter-spacing: 1px; line-height: 1;
  }
  .brand-dot { width: 9px; height: 9px; border-radius: 50%; background: var(--green); }
  .salutation {
    position: absolute; left: 65px; top: 310px;
    font-family: "Questrial", sans-serif; font-weight: 700;
    font-size: 16.5px; color: var(--ink);
  }
  .letter-body {
    position: absolute; left: 64px; top: 356px; width: 584px;
    font-family: "Arimo", sans-serif; font-size: 11.4px; line-height: 14.6px;
    color: var(--ink); text-align: justify;
  }
  .letter-body p { margin-bottom: 12.4px; }
  .closing {
    position: absolute; left: 65px; top: 660px;
    font-family: "Questrial", sans-serif; font-weight: 700; font-size: 9px; color: var(--ink);
  }
  .signature {
    position: absolute; left: 64px; top: 702px; width: 118px; height: 34px;
    background: linear-gradient(90deg, #e6e6e6, #f2f2f2);
  }
  .contact-footer {
    position: absolute; left: 0; right: 0; top: 948px;
    font-family: "Arimo", sans-serif; font-size: 11.8px; color: var(--footer-ink);
    text-align: center;
  }
  .address {
    width: 384px; margin: 0 auto; padding-bottom: 2px;
    border-bottom: 1px solid var(--footer-ink);
  }
  .contact-row {
    display: flex; justify-content: center; align-items: center; gap: 10px; margin-top: 4px;
  }
  .contact-item { display: flex; align-items: center; gap: 8px; }
  .contact-item svg { width: 9px; height: 9px; fill: var(--green); }
</style>
</head>
<body>
  <article class="letterhead">
    <header class="masthead">
      <span class="brand">tarra kelo</span>
      <span class="brand-dot"></span>
    </header>

    <h2 class="salutation">Dear Mr. Smith,</h2>

    <section class="letter-body">
      <p>Lorem ipsum dolor sit amet, consectetuer adipiscing elit, sed diam nonmmy nibh euismod tincidunt ut laor eet dolore magna aliquam erat volutpat. Ut wisi enim ad minim veniam, quis nostrud exerci tationmcorper suscipit lobortis nisl ut aliquip ex ea commodo consequat. Duis autem vel eum iriure dolor in hendrerit in vulputate velit esse molestie consequat, vel illum dolore eu feugiat</p>
      <p>Rorem ipsum dolor sit amet, consectetuer adipiscing elit, sed diam nonmmy nibh euismod tincidunt ut laor eet dolore magna aliquam erat volutpat. Ut wisi enim ad minim veniam, quis nostrud exerci tationmcorper suscipit lobortis nisl ut aliquip ex ea commodo consequat. Duis autem vel eum iriure dolor in hendrerit in vulputate velit esse molest</p>
      <p>Dorem ipsum dolor sit amet, consectetuer adipiscing elit, sed diam nonmmy nibh euismod tincidunt ut laor eet dolore magna aliquam erat volutpat. Ut wisi enim ad minim veniam, quis nostrud exerci tationmcorper suscipit lobortis nisl ut aliquip ex ea commodo consequat. Duis autem vel eum iriure dolor in hendrerit in suscipit lobortis nisl ut aliquip ex ea commodo consequat. Duis autem vel eum iriure dolor in hendrerit in vulputate velit esse molestie consequat, vel illum</p>
      <p>Sorem ipsum dolor sit amet, consectetuer adipiscing elit, sed diam nonmmy nibh euismod tincidunt ut laor eet dolore magna aliquam erat volutpat. Ut wisi enim ad minim veniam, quis nostrud exerci tationmcorper suscipit lobortis nisl ut aliquip ex ea commodo consequat. Duis autem vel eum iriure dolor in</p>
    </section>

    <p class="closing">Sincerely,</p>
    <div class="signature" role="img" aria-label="Handwritten signature of the sender"></div>

    <footer class="contact-footer">
      <div class="address">Your address, city, state, ZIP 0000</div>
      <div class="contact-row">
        <span class="contact-item">
          <svg viewBox="0 0 10 10" aria-hidden="true"><path d="M2 0.5 L3.6 2.6 L2.8 3.6 Q3.8 5.9 6.4 7.2 L7.4 6.4 L9.5 8 L8.4 9.6 Q4.5 9.4 1.8 6.4 Q0.2 4.2 0.4 1.6 Z"/></svg>
          555-010-2100
        </span>
        <span class="contact-item">
          <svg viewBox="0 0 10 10" aria-hidden="true"><path d="M0 2 H10 V8 H0 Z M0.8 2.6 L5 5.6 L9.2 2.6" stroke="#fff" stroke-width="0.8"/></svg>
          info@tarrakelo.com
        </span>
        <span class="contact-item">
          <svg viewBox="0 0 10 10" aria-hidden="true"><circle cx="5" cy="5" r="4.6"/><path d="M0.6 5 H9.4 M5 0.5 Q2.6 5 5 9.5 M5 0.5 Q7.4 5 5 9.5" stroke="#fff" stroke-width="0.7" fill="none"/></svg>
          www.tarrakelo.com
        </span>
      </div>
    </footer>
  </article>
</body>
</html>
```